RM Tomás Ledesma (Business Card)

Hi designers, in this work, I'm looking for an sophisticated stylish, elegant and proffesional personal card. We have a laboratory of pathology automated, with equipments high quality.
In this web the designers, have created my business logo, the name is "RM Tomás Ledesma"
In our lab, we principal work is to prepare the biopsies for further diagnostic of diseases like cancer, tumors, etc.
I need that the first face, only having my complete logo (Rm Tomás Ledesma, Laboratorio de procesamiento Histologico)
The overleaf, could repeat the same logo, like water logo.
In this face, I need to say: My full data:

Técnico en Anatomía Patológica
Tomás Ledesma Urquiza M.P 48213
Av. Duarte Quirós 817 - 2do piso - Instituto Brandsen.
Córdoba, Argentina
(0351) 158246093
ledesma.tomas@correoviva.com.ar

with respect the colors of card, use your imagination, the original logo color is violet, I haven't chosen a color base for the card.

attached pictures are examples of cards I like your DESIGN.
Attached too, the original logo to my company.

the size of card are:
horizontal: 9cm
vertical: 5,5cm

any question that you have, not doubt to question me,
Hand to work!

Industry/Entity Type

Laboratory

Requirements
Must have
• designers sophisticated, not simples, like show the images attached

```html
<!DOCTYPE html>
<html lang="es">
<head>
<meta charset="utf-8">
<title>Tomás Ledesma – Papelería</title>
<link href="https://fonts.googleapis.com/css2?family=PT+Sans+Narrow:wght@700&family=Didact+Gothic&display=swap" rel="stylesheet">
<style>
  :root{
    --violet:#5a2a86;
    --violet-soft:#7a4fa6;
    --paper:#f7f7f8;
    --paper-shade:#e4e4e7;
    --ink:#5d5d63;
    --ink-light:#9a9aa1;
    --stage:#e6e4ea;
    --white:#ffffff;
  }
  *{box-sizing:border-box;margin:0;padding:0}
  html,body{width:1200px;height:900px;overflow:hidden}
  body{background:var(--stage);font-family:"Didact Gothic",sans-serif;color:var(--ink);position:relative}

  .sheet{position:absolute;background:linear-gradient(160deg,var(--white) 0%,var(--paper) 55%,var(--paper-shade) 100%);overflow:hidden;box-shadow:0 4px 14px rgba(40,20,60,.18)}
  .band{position:absolute;left:0;bottom:0;width:100%;display:block}

  /* Logo lockup */
  .lockup{position:absolute;display:flex;flex-direction:column;align-items:center}
  .lockup .mark-row{display:flex;align-items:center;gap:6px}
  .lockup .dot{border-radius:50%;background:var(--violet)}
  .lockup .name{font-family:"PT Sans Narrow",sans-serif;font-weight:700;color:var(--violet);letter-spacing:.18em;text-transform:uppercase;white-space:nowrap}
  .lockup .rule{height:1px;background:var(--ink-light);width:100%}
  .lockup .lab{font-family:"PT Sans Narrow",sans-serif;font-weight:700;color:var(--ink);text-transform:uppercase;white-space:nowrap;letter-spacing:.01em}

  /* Letterhead */
  .letterhead{left:190px;top:50px;width:500px;height:706px}
  .letterhead .lockup{left:0;right:0;top:26px}
  .letterhead .name{font-size:15px}
  .letterhead .dot{width:10px;height:10px}
  .letterhead .lab{font-size:15px;margin-top:2px}
  .letterhead .rule{width:200px;margin-top:3px}
  .letterhead .header-line{position:absolute;left:18px;right:0;top:92px;height:3px;background:var(--violet)}
  .letterhead .watermark{position:absolute;left:0;right:0;top:330px;text-align:center;font-family:"PT Sans Narrow",sans-serif;font-weight:700;font-size:54px;letter-spacing:.12em;text-transform:uppercase;color:rgba(90,90,100,.08)}
  .letterhead .footer{position:absolute;left:0;right:0;bottom:18px;color:var(--white);font-size:11px;text-align:center}
  .letterhead .footer .contacts{display:flex;justify-content:center;gap:60px;margin-bottom:14px}
  .contact{display:inline-flex;align-items:center;gap:6px}
  .contact svg{flex:none}

  /* Envelope */
  .envelope{left:725px;top:90px;width:440px;height:250px}
  .envelope .lockup{left:22px;top:22px;align-items:flex-start}
  .envelope .name{font-size:9px}
  .envelope .dot{width:7px;height:7px}
  .envelope .lab{font-size:9px;margin-top:1px}
  .envelope .rule{width:110px;margin-top:2px}

  /* Cards */
  .card{width:262px;height:160px;border-radius:10px}
  .card-front{left:810px;top:420px}
  .card-front .lockup{left:0;right:0;top:22px}
  .card-front .name{font-size:10px}
  .card-front .dot{width:8px;height:8px}
  .card-front .lab{font-size:10.5px;margin-top:1px}
  .card-front .rule{width:120px;margin-top:2px}
  .card-front .watermark{position:absolute;left:0;right:0;bottom:18px;text-align:center;font-family:"PT Sans Narrow",sans-serif;font-weight:700;font-size:15px;letter-spacing:.18em;text-transform:uppercase;color:rgba(255,255,255,.12)}

  .card-back{left:810px;top:610px}
  .card-back .lockup{left:0;right:0;top:14px}
  .card-back .name{font-size:7.5px}
  .card-back .dot{width:6px;height:6px}
  .card-back .lab{font-size:8px}
  .card-back .rule{width:90px;margin-top:1px}
  .card-back .address{position:absolute;left:0;right:0;top:50px;text-align:center;font-size:5.5px;line-height:1.35;color:var(--ink-light)}
  .card-back .holder{position:absolute;left:20px;top:80px;font-size:5.5px;line-height:1.5;color:var(--violet-soft)}
  .card-back .holder .full-name{font-size:9px;color:var(--ink);margin-bottom:2px}
  .card-back .divider{position:absolute;left:152px;top:76px;width:1px;height:42px;background:var(--ink-light)}
  .card-back .reach{position:absolute;left:160px;top:82px;font-size:5.5px;line-height:2.2;color:var(--ink-light)}
</style>
</head>
<body>

  <!-- Letterhead -->
  <section class="sheet letterhead" aria-label="Hoja membretada">
    <div class="lockup">
      <div class="mark-row"><span class="dot"></span><span class="name">RM Tomás Ledesma</span></div>
      <span class="rule"></span>
      <span class="lab">Laboratorio de procesamiento histologico</span>
    </div>
    <div class="header-line"></div>
    <div class="watermark">Tomás Ledesma</div>
    <svg class="band" viewBox="0 0 500 150" height="150" preserveAspectRatio="none" aria-hidden="true">
      <path d="M0 58 Q230 -2 500 22" fill="none" stroke="#c9c9ce" stroke-width="3"/>
      <path d="M0 78 Q240 6 500 36 L500 150 L0 150 Z" fill="var(--violet)"/>
    </svg>
    <div class="footer">
      <div class="contacts">
        <span class="contact">
          <svg width="7" height="11" viewBox="0 0 7 11"><rect x=".5" y=".5" width="6" height="10" rx="1" fill="none" stroke="#fff"/><circle cx="3.5" cy="8.6" r=".7" fill="#fff"/></svg>
          (0351) 158246093
        </span>
        <span class="contact">
          <svg width="11" height="8" viewBox="0 0 11 8"><rect x=".5" y=".5" width="10" height="7" fill="none" stroke="#fff"/><path d="M.5 .5 L5.5 4.5 L10.5 .5" fill="none" stroke="#fff"/></svg>
          ledesma.tomas@correoviva.com.ar
        </span>
      </div>
      <div class="address">Av. Duarte Quirós 817 - 2do piso - Instituto Brandsen, Córdoba, Argentina</div>
    </div>
  </section>

  <!-- Envelope -->
  <section class="sheet envelope" aria-label="Sobre">
    <div class="lockup">
      <div class="mark-row"><span class="dot"></span><span class="name">RM Tomás Ledesma</span></div>
      <span class="rule"></span>
      <span class="lab">Laboratorio de procesamiento histologico</span>
    </div>
    <svg class="band" viewBox="0 0 440 80" height="80" preserveAspectRatio="none" aria-hidden="true">
      <path d="M0 62 Q200 4 440 8" fill="none" stroke="#c9c9ce" stroke-width="2.5"/>
      <path d="M0 80 Q210 16 440 20 L440 80 Z" fill="var(--violet)"/>
    </svg>
  </section>

  <!-- Business card: front -->
  <section class="sheet card card-front" aria-label="Tarjeta personal, frente">
    <div class="lockup">
      <div class="mark-row"><span class="dot"></span><span class="name">RM Tomás Ledesma</span></div>
      <span class="rule"></span>
      <span class="lab">Laboratorio de procesamiento histologico</span>
    </div>
    <svg class="band" viewBox="0 0 262 80" height="80" preserveAspectRatio="none" aria-hidden="true">
      <path d="M0 22 Q130 2 262 10" fill="none" stroke="#c9c9ce" stroke-width="2"/>
      <path d="M0 36 Q140 6 262 16 L262 80 L0 80 Z" fill="var(--violet)"/>
    </svg>
    <div class="watermark">Tomás Ledesma</div>
  </section>

  <!-- Business card: back -->
  <section class="sheet card card-back" aria-label="Tarjeta personal, dorso">
    <div class="lockup">
      <div class="mark-row"><span class="dot"></span><span class="name">RM Tomás Ledesma</span></div>
      <span class="rule"></span>
      <span class="lab">Laboratorio de procesamiento histologico</span>
    </div>
    <p class="address">Av. Duarte Quirós 817 - 2do piso - Instituto Brandsen<br>Córdoba, Argentina</p>
    <div class="holder">
      <p class="full-name">Tomás Ledesma Urquiza</p>
      <p>Técnico en Anatomía Patológica</p>
      <p>M.P 48213</p>
    </div>
    <div class="divider"></div>
    <div class="reach">
      <p class="contact">
        <svg width="5" height="7" viewBox="0 0 5 7"><rect x=".4" y=".4" width="4.2" height="6.2" rx=".6" fill="none" stroke="#7a4fa6" stroke-width=".8"/></svg>
        (0351) 158246093
      </p>
      <p class="contact">
        <svg width="7" height="5" viewBox="0 0 7 5"><rect width="7" height="5" fill="#7a4fa6"/><path d="M0 0 L3.5 2.6 L7 0" fill="none" stroke="#fff" stroke-width=".6"/></svg>
        ledesma.tomas@correoviva.com.ar
      </p>
    </div>
    <svg class="band" viewBox="0 0 262 30" height="30" preserveAspectRatio="none" aria-hidden="true">
      <path d="M0 28 Q130 6 262 8" fill="none" stroke="#c9c9ce" stroke-width="1.5"/>
      <path d="M0 30 Q140 12 262 14 L262 30 Z" fill="var(--violet)"/>
    </svg>
  </section>

</body>
</html>
```